Defense contractor needs a roll-up for an exhibition

The booth we have booked has only a size of 3m².
So this will be the centerpiece of the whole booth.
We need a roll-up that attracts visitors and at the same time it should contain already designed graphics. These graphics are giving visitors an overview of our system. So it is necessary to have them exposed in a height that the booth personal can conveniently point with its fingers at them.
For information about our company and product visit:
https://www.brellowtrackline.com/
For designing you should use Adobe Illustrator and the templates provided in the zip file, to guarantee a perfect print.
I have supplied my business card that you can copy the logo. As the company logo will be already at the booth nearby the top of the roll-up, you should not place it there. It can be in the middle or at the bottom.
I have uploaded a picture of the booth. The roll up will be placed at the left of the screen and has a size of 80cm x 200cm

Defense

Defense

Serif

0054AA
0677BA
7BADD7
CADEEF
E8F1F8

• you must use the Adobe Illustrator template to have a good printing result
• company logo on the upper side of the roll-up

```html
<!DOCTYPE html>
<html lang="en">
<head>
<meta charset="utf-8">
<title>Brellow Trackline – Exhibition Roll-up</title>
<link rel="stylesheet" href="https://fonts.googleapis.com/css2?family=Arimo:wght@400&family=Barlow+Condensed:ital,wght@0,800;1,800&family=Barlow+Semi+Condensed:wght@700&display=swap">
<style>
  :root {
    --stage: #3d3d40;
    --panel: #eef0f8;
    --ink: #111113;
    --white: #ffffff;
    --accent: #e8772e;
    --sky-deep: #050608;
    --sky-blue: #2d4f9c;
    --sky-pink: #d98aa6;
    --sky-glow: #f0b7a8;
    --chevron-shadow: #55565b;
    --visual-light: #e6e9f4;
    --visual-mid: #cfd5ea;
  }
  * { box-sizing: border-box; margin: 0; padding: 0; }
  html, body { width: 1200px; height: 2291px; overflow: hidden; background: var(--stage); }
  .rollup {
    position: absolute; left: 159px; top: 62px;
    width: 882px; height: 2168px;
    background: var(--panel);
    border-top: 3px solid var(--accent);
    border-bottom: 3px solid var(--accent);
    overflow: hidden;
    font-family: "Barlow Condensed", "Arial Narrow", sans-serif;
    color: var(--ink);
  }
  .hero { position: absolute; left: 0; top: 0; width: 882px; height: 900px; }
  .headline {
    position: absolute; left: 0; top: 100px; width: 882px;
    text-align: center; color: var(--white);
    font-style: italic; font-weight: 800; font-size: 86px; line-height: 83px;
    text-transform: uppercase;
  }
  .brand {
    position: absolute; left: 78px; top: 936px;
    font-weight: 800; font-size: 64px; line-height: 80px;
    text-transform: uppercase; color: var(--ink);
  }
  .system-visual {
    position: absolute; left: 46px; top: 1040px; width: 790px; height: 500px;
    background: linear-gradient(160deg, var(--visual-light), var(--visual-mid));
    border-radius: 6px;
  }
  .services { position: absolute; left: 87px; top: 1565px; width: 760px; }
  .services-title {
    font-family: "Barlow Semi Condensed", "Arial Narrow", sans-serif;
    font-weight: 700; font-size: 52px; line-height: 58px;
    padding-bottom: 2px; width: 266px; border-bottom: 4px solid var(--ink);
  }
  .services-intro, .services-outro {
    font-family: "Barlow Semi Condensed", "Arial Narrow", sans-serif;
    font-weight: 700; font-size: 32px; line-height: 37.5px;
  }
  .services-intro { margin-top: 20px; }
  .offer-list { list-style: none; margin-top: 20px; }
  .offer-list li {
    display: flex; align-items: center; gap: 26px;
    font-family: "Arimo", Arial, sans-serif; font-size: 33px; line-height: 37.5px;
  }
  .offer-list svg { width: 30px; height: 30px; flex: none; }
  .services-outro { margin-top: 18px; }
</style>
</head>
<body>
  <main class="rollup">
    <svg class="hero" viewBox="0 0 882 900" role="img" aria-label="Dusk sky with a main battle tank silhouette standing in grass">
      <defs>
        <linearGradient id="sky" x1="0" y1="0" x2="0" y2="1">
          <stop offset="0" stop-color="var(--sky-deep)"/>
          <stop offset="0.3" stop-color="var(--sky-deep)"/>
          <stop offset="0.45" stop-color="var(--sky-blue)"/>
          <stop offset="0.58" stop-color="var(--sky-pink)"/>
          <stop offset="0.68" stop-color="var(--sky-glow)"/>
          <stop offset="0.78" stop-color="var(--sky-blue)"/>
          <stop offset="0.88" stop-color="#1a1c26"/>
          <stop offset="1" stop-color="#000"/>
        </linearGradient>
        <radialGradient id="shade" cx="0.55" cy="0.82" r="0.45">
          <stop offset="0" stop-color="#000" stop-opacity="0.85"/>
          <stop offset="1" stop-color="#000" stop-opacity="0"/>
        </radialGradient>
      </defs>
      <polygon points="0,728 441,892 882,728 882,760 441,895 0,760" fill="var(--chevron-shadow)"/>
      <polygon points="0,0 882,0 882,728 441,858 0,728" fill="url(#sky)"/>
      <polygon points="0,0 882,0 882,728 441,858 0,728" fill="url(#shade)"/>
    </svg>

    <h1 class="headline">Advanced Combat<br>Training Systems for<br>Realistic Combat<br>Simulation</h1>

    <div class="brand">Brellow Trackline</div>

    <div class="system-visual" role="img" aria-label="System overview graphic: two tanks, three pop-up targets and a control truck with operator screens"></div>

    <section class="services">
      <h2 class="services-title">Services</h2>
      <p class="services-intro">The signature of the contract is not the end<br>it is just the beginning of a long-lasting partnership.<br>We offer</p>
      <ul class="offer-list">
        <li><svg viewBox="0 0 30 30"><circle cx="14" cy="16" r="11" fill="none" stroke="#111" stroke-width="2.4"/><path d="M8 15l5 5 13-14" fill="none" stroke="#111" stroke-width="2.6"/></svg>extended warranty programs</li>
        <li><svg viewBox="0 0 30 30"><circle cx="14" cy="16" r="11" fill="none" stroke="#111" stroke-width="2.4"/><path d="M8 15l5 5 13-14" fill="none" stroke="#111" stroke-width="2.6"/></svg>logistics support</li>
        <li><svg viewBox="0 0 30 30"><circle cx="14" cy="16" r="11" fill="none" stroke="#111" stroke-width="2.4"/><path d="M8 15l5 5 13-14" fill="none" stroke="#111" stroke-width="2.6"/></svg>maintenance contracts</li>
        <li><svg viewBox="0 0 30 30"><circle cx="14" cy="16" r="11" fill="none" stroke="#111" stroke-width="2.4"/><path d="M8 15l5 5 13-14" fill="none" stroke="#111" stroke-width="2.6"/></svg>long-term spare part services</li>
      </ul>
      <p class="services-outro">to keep the equipment in perfect operational condition</p>
    </section>
  </main>
</body>
</html>
```